Stationery Design Project for Nimbora, Chicago

Nimbora, a street parking application which helps car drivers find a street parking spot by offering an ideal path along which to look for parking. This path is calculated by our algorithm based on data (e.g. historical data, baseball games schedule, etc.). Along this path the driver will find a spot and will also save 70% of the search time. Customer we target is reg. between 21 and 45 yo.

We envision something young, fresh, bright and original. Slightly abstract maybe. It should represent the idea and elements of finding street parking in the city, e.g. car(s), parking spot, people, city, etc. (just ideas!).

Logo is attached.

Requirement:
- Business Cards (2 Sided Full Color CMYK)
- Letterhead (1 Sided Full Color CMYK)
- Envelope (1 Sided Full Color CMYK)
- Sticker (1 Sided Full Color CMYK), round with a 2inch diameter.

Reason: We're starting to get more and more designs and need more time to look into all of them. Very exciting!! Thanks to everybody!

Hi all, we're in the process of selecting our favs. Though choices!!! Really good submissions. Will keep you posted and sorry for the delay.

Target Market(s)

Car drivers and owners between 21 and 45

Industry/Entity Type

Parking

Requirements
Must have
• Sticker should be round and include company URL nimbora.com and the new logo which we will attach soon.
Should not have
• Should not be too serious or boring.

```html
<!DOCTYPE html>
<html lang="en">
<head>
<meta charset="utf-8">
<title>Nimbora Envelope Stationery</title>
<link rel="stylesheet" href="https://fonts.googleapis.com/css2?family=Open+Sans:wght@300;600&display=swap">
<style>
  :root {
    --paper: #ffffff;
    --ink: #3a3a3c;
    --text: #444446;
    --frame: #1a1a1a;
    --divider: #9cc7e6;
    --skyline-light: #fde6c2;
    --skyline: #fbd28f;
  }
  html, body {
    margin: 0;
    padding: 0;
    width: 1200px;
    height: 904px;
    overflow: hidden;
    background: var(--paper);
  }
  .canvas {
    position: relative;
    width: 1200px;
    height: 904px;
    font-family: "Open Sans", Arial, sans-serif;
  }
  .envelope {
    position: absolute;
    width: 830px;
    height: 360px;
    border: 1px solid var(--frame);
    background: var(--paper);
    box-sizing: border-box;
    overflow: hidden;
  }
  .envelope--stacked { left: 238px; top: 91px; }
  .envelope--inline { left: 234px; top: 480px; height: 361px; }

  .brand {
    position: absolute;
    margin: 0;
    font-size: 36px;
    font-weight: 600;
    color: var(--ink);
    letter-spacing: -0.5px;
    line-height: 1;
    white-space: nowrap;
  }
  .envelope--stacked .brand { left: 22px; top: 34px; }
  .envelope--inline .brand { left: 18px; top: 35px; }

  .address {
    position: absolute;
    margin: 0;
    font-size: 9.5px;
    font-weight: 300;
    color: var(--text);
    white-space: nowrap;
    line-height: 1.2;
  }
  .address__sep {
    color: var(--divider);
    margin: 0 10px;
  }
  .envelope--stacked .address { left: 87px; top: 74px; }
  .envelope--inline .address { left: 237px; top: 47px; }

  .skyline {
    position: absolute;
    border-radius: 50% 50% 0 0 / 70% 70% 0 0;
    background: linear-gradient(180deg, var(--skyline-light), var(--skyline));
    opacity: 0.85;
  }
  .envelope--stacked .skyline { left: 8px; top: 181px; width: 256px; height: 178px; }
  .envelope--inline .skyline { left: 634px; top: 236px; width: 182px; height: 124px; }
</style>
</head>
<body>
<main class="canvas">
  <section class="envelope envelope--stacked">
    <p class="brand">nimbora</p>
    <p class="address">210 Wacker Lane, Suite 4<span class="address__sep">|</span>Chicago, IL 60606<span class="address__sep">|</span>www.nimbora.com</p>
    <div class="skyline" role="img" aria-label="Line illustration of city skyscrapers under a dome arc in pale orange"></div>
  </section>

  <section class="envelope envelope--inline">
    <p class="brand">nimbora</p>
    <p class="address">210 Wacker Lane, Suite 4<span class="address__sep">|</span>Chicago, IL 60606</p>
    <div class="skyline" role="img" aria-label="Line illustration of city skyscrapers under a dome arc in pale orange"></div>
  </section>
</main>
</body>
</html>
```